Flyer for the Lumen 2025 Conference

I am looking to produce a flyer for our upcoming conference, Lumen 2025. This is an annual conference that we plan to publicize on social media. The ideal designer will create a flyer that is eye-catching and effectively communicates the key information. Please see attached our logo, speaker photo, and flyer content.

Target Market(s)

All demographics

Industry/Entity Type

Christian

Font styles to use
Sans Serif

Requirements
Should not have
• Cross, church

```html
<!DOCTYPE html>
<html lang="en">
<head>
<meta charset="utf-8">
<title>Lumen 2025 Conference Flyer</title>
<link href="https://fonts.googleapis.com/css2?family=Anton&family=Russo+One&family=Oswald:wght@600;700&family=Poppins:wght@400;500;600;700&display=swap" rel="stylesheet">
<style>
:root{
  --navy-deep:#041431;
  --navy:#0a2552;
  --blue:#1f6fd1;
  --sky:#3fa3ea;
  --gold:#f5c518;
  --orange:#e8780f;
  --white:#ffffff;
}
*{margin:0;padding:0;box-sizing:border-box}
html,body{width:1004px;height:1200px;overflow:hidden;background:var(--navy-deep)}
.flyer{position:relative;width:1004px;height:1200px;overflow:hidden;
  background:radial-gradient(ellipse at 45% 25%,#143772 0%,var(--navy) 40%,var(--navy-deep) 100%);
  font-family:'Poppins',sans-serif;color:var(--white)}
.speaker-photo{position:absolute;left:0;top:330px;width:560px;height:870px;
  border-radius:240px 240px 0 0;
  background:linear-gradient(180deg,rgba(31,111,209,.5) 0%,rgba(20,74,160,.45) 60%,rgba(4,20,49,.15) 100%)}
.brand{position:absolute;left:80px;top:62px;width:220px;text-align:center}
.brand-name{font-weight:600;font-size:44px;letter-spacing:1px;line-height:1}
.brand-tag{font-weight:500;font-size:11.5px;letter-spacing:.5px;color:var(--orange);margin-top:6px}
.title{position:absolute;left:361px;top:40px;font-family:'Anton',sans-serif;font-size:197px;line-height:1;white-space:nowrap;
  background:linear-gradient(90deg,#e8780f 0%,#f2a21a 50%,#f8d21c 100%);-webkit-background-clip:text;background-clip:text;color:transparent;letter-spacing:4px}
.year{position:absolute;left:366px;top:226px;font-family:'Russo One',sans-serif;font-size:205px;line-height:1;
  transform:scaleX(.74);transform-origin:left top;white-space:nowrap;
  background:linear-gradient(180deg,#ffffff 0%,#eef0f3 55%,#c9ccd3 56%,#dfe2e7 100%);-webkit-background-clip:text;background-clip:text;color:transparent}
.subtitle{position:absolute;left:364px;top:425px;font-family:'Oswald',sans-serif;font-weight:700;font-size:64px;line-height:60px;text-transform:uppercase}
.subtitle .lead{background:linear-gradient(90deg,#1f6fd1,#4aa8ee);-webkit-background-clip:text;background-clip:text;color:transparent}
.topic{position:absolute;left:414px;top:577px}
.topic-label{color:var(--gold);font-size:28px;font-weight:500;line-height:34px}
.topic-title{font-size:33px;font-weight:700;line-height:37px;text-transform:uppercase}
.topic-title span{font-weight:400}
.venue{position:absolute;left:414px;top:716px}
.venue-name{color:var(--sky);font-size:24px;font-weight:600;line-height:29px}
.venue-address{display:flex;gap:6px;margin-top:8px;font-size:19.5px;line-height:25px}
.venue-address svg{flex:none;margin-top:3px}
.dates{position:absolute;left:757px;top:305px;width:162px}
.day{position:relative;height:154px;margin-bottom:22px;border:2px solid var(--blue);background:rgba(4,20,49,.4)}
.day-name{position:absolute;top:-8px;left:26px;width:110px;height:32px;background:var(--orange);
  font-family:'Oswald',sans-serif;font-weight:700;font-size:23px;line-height:32px;text-align:center}
.day-num{position:absolute;top:30px;left:0;width:100%;text-align:center;font-weight:700;font-size:68px;line-height:72px}
.day-num sup{position:absolute;top:6px;left:118px;font-size:12px;font-weight:400;line-height:1}
.day-month{position:absolute;top:102px;width:100%;text-align:center;color:var(--gold);font-size:17px;letter-spacing:3px}
.day-time{position:absolute;bottom:-2px;left:-2px;right:-2px;height:28px;background:linear-gradient(90deg,#2d86dc,#4aa8ee);
  font-size:14px;font-weight:500;line-height:28px;text-align:center}
.day-time i{display:inline-block;width:12px;height:12px;border-radius:50%;background:var(--gold);vertical-align:-1px;margin:0 4px}
.app{position:absolute;left:625px;top:862px}
.app-head{font-size:31px;font-weight:700;line-height:33px}
.app-head span{color:var(--gold);display:block}
.app-sub{font-size:14.5px;font-weight:700;margin-top:4px;letter-spacing:.2px}
.stores{display:flex;gap:9px;margin-top:9px}
.store{width:139px;height:42px;background:var(--white);border-radius:5px;color:#111;font-size:15px;font-weight:500;
  display:flex;align-items:center;justify-content:center;gap:8px}
.store i{width:14px;height:14px;border-radius:50%;background:#111}
.contact{position:absolute;left:632px;top:1034px;font-size:26px;line-height:34px}
.contact li{list-style:none;display:flex;align-items:center;gap:10px}
.contact .phone{font-weight:700}
.speaker{position:absolute;left:81px;top:1005px}
.speaker-label{color:var(--gold);font-size:29px;font-weight:700;line-height:32px}
.speaker-name{font-size:45px;font-weight:700;line-height:50px;text-transform:uppercase}
</style>
</head>
<body>
<main class="flyer">
  <div class="speaker-photo" role="img" aria-label="Photo of the speaker in a blue suit, seated"></div>

  <header class="brand">
    <div class="brand-name">KAIRETH</div>
    <div class="brand-tag">A LIGHT TO EVERY LAND</div>
  </header>

  <h1 class="title">LUMEN</h1>
  <div class="year">2025</div>
  <h2 class="subtitle"><span class="lead">A Prophetic</span><br>Conference</h2>

  <section class="topic">
    <div class="topic-label">TOPIC:</div>
    <div class="topic-title">The Voice <span>of</span><br>The Lord</div>
  </section>

  <section class="venue">
    <div class="venue-name">The Harborview<br>Performing Arts Center</div>
    <div class="venue-address">
      <svg width="16" height="20" viewBox="0 0 16 20"><path d="M8 0a8 8 0 0 0-8 8c0 6 8 12 8 12s8-6 8-12a8 8 0 0 0-8-8z" fill="#3fa3ea"/><circle cx="8" cy="8" r="3" fill="#0a2552"/></svg>
      <div>218 Linden Avenue<br>Eastfield, Maine 04010</div>
    </div>
  </section>

  <section class="dates">
    <div class="day"><div class="day-name">FRIDAY</div><div class="day-num">26<sup>TH</sup></div><div class="day-month">DECEMBER</div><div class="day-time">6:30PM<i></i>9:00PM</div></div>
    <div class="day"><div class="day-name">SATURDAY</div><div class="day-num">27<sup>TH</sup></div><div class="day-month">DECEMBER</div><div class="day-time">5:30PM<i></i>8:00PM</div></div>
    <div class="day"><div class="day-name">SUNDAY</div><div class="day-num">28<sup>TH</sup></div><div class="day-month">DECEMBER</div><div class="day-time">4:30PM<i></i>7:00PM</div></div>
  </section>

  <section class="app">
    <div class="app-head">Download the<span>KAIRETH App</span></div>
    <div class="app-sub">TO STAY UPDATED ON THE EVENT</div>
    <div class="stores">
      <div class="store"><i></i>Mobile Store</div>
      <div class="store"><i></i>Tablet Store</div>
    </div>
  </section>

  <ul class="contact">
    <li class="phone"><svg width="18" height="18" viewBox="0 0 24 24"><path d="M6.6 10.8a15 15 0 0 0 6.6 6.6l2.2-2.2a1 1 0 0 1 1-.25 11.4 11.4 0 0 0 3.6.57 1 1 0 0 1 1 1V20a1 1 0 0 1-1 1A17 17 0 0 1 3 4a1 1 0 0 1 1-1h3.5a1 1 0 0 1 1 1c0 1.25.2 2.450.57 3.57a1 1 0 0 1-.25 1z" fill="#3fa3ea"/></svg>207 555 0142</li>
    <li><svg width="18" height="16" viewBox="0 0 24 20"><rect x="1" y="2" width="22" height="16" rx="2" fill="#3fa3ea"/><path d="M2 4l10 7 10-7" stroke="#0a2552" stroke-width="2" fill="none"/></svg>hello@kaireth.org</li>
    <li><svg width="18" height="18" viewBox="0 0 24 24"><circle cx="12" cy="12" r="10" fill="none" stroke="#3fa3ea" stroke-width="2"/><path d="M2 12h20M12 2c3 3 3 17 0 20M12 2c-3 3-3 17 0 20" stroke="#3fa3ea" stroke-width="2" fill="none"/></svg>www.kaireth.org</li>
  </ul>

  <section class="speaker">
    <div class="speaker-label">SPEAKER</div>
    <div class="speaker-name">Prophet<br>Samuel Adeyo</div>
  </section>
</main>
</body>
</html>
```